Harbourline Physiotherapy business card design

We need a fresh, new business card design for our physiotherapy clinic Harbourline Physiotherapy

Will attach logo soon we had logo designed from our last project

Industry/Entity Type

Physical Therapy

Contact Information for Business Card

On front
Needs our logo, contact details:
58 Wexley Lane Marrowdale NSW 2791
Ph/f: 02 9481 2057
info@harbourlinephysio.example.com.au

Requirements
Must have
• On the back of the card needs to have area to write down follow up appointments
• On front
• Needs our logo
• The colours have to be the colours in our logo which are: sky blue, black and white
• Font to be same as our logo please
• We want the card to look simple, not too cluttered but to the point
Should not have
• We don't need any extra pictures other than our logo

```html
<!DOCTYPE html>
<html lang="en">
<head>
<meta charset="utf-8">
<title>Harbourline Physiotherapy – Business Card</title>
<link rel="stylesheet" href="https://fonts.googleapis.com/css2?family=Open+Sans:wght@400;600;700&display=swap">
<style>
  :root {
    --sky: #1f7fd0;
    --navy: #1d3f9c;
    --ink: #3a3a3a;
    --muted: #6d6d6d;
    --rule: #2a6fc4;
    --paper: #ffffff;
    --stage: #e9ebee;
    --band-dark: #1b2f8a;
    --band-light: #4aa3e0;
    --swoosh: #454545;
    --divider: #c9c9c9;
  }
  * { box-sizing: border-box; margin: 0; padding: 0; }
  html, body { width: 1200px; height: 843px; overflow: hidden; }
  body {
    background: var(--stage);
    font-family: "Open Sans", Arial, sans-serif;
    color: var(--ink);
    position: relative;
  }
  .card {
    position: absolute;
    width: 540px;
    height: 310px;
    background: var(--paper);
    box-shadow: 0 6px 18px rgba(0,0,0,.18);
    overflow: hidden;
  }

  /* ---------- Back: appointment card ---------- */
  .card--back { left: 50px; top: 110px; }
  .back__title {
    position: absolute; right: 34px; top: 24px;
    font-size: 20px; font-weight: 700; color: var(--sky);
  }
  .field {
    position: absolute; display: flex; align-items: flex-end;
    font-size: 14px; font-weight: 600; color: var(--sky);
  }
  .field__line {
    flex: 1; margin-left: 6px; border-bottom: 1.5px dotted var(--rule); height: 1px;
  }
  .field--name { left: 40px; right: 200px; top: 74px; }
  .field--time { left: 370px; right: 34px; top: 74px; }
  .field--time .ampm {
    position: absolute; right: 0; top: -14px; font-size: 10px; font-weight: 400;
  }
  .field--date { left: 40px; right: 34px; top: 110px; }
  .days {
    position: absolute; left: 40px; right: 34px; top: 146px;
    display: flex; justify-content: space-between;
    font-size: 13px; color: var(--sky); font-weight: 600;
  }
  .day { display: flex; align-items: center; gap: 5px; }
  .day__box { width: 13px; height: 13px; border: 1.3px solid var(--ink); }
  .field--note { left: 40px; right: 34px; top: 186px; }
  .blank-line {
    position: absolute; left: 40px; right: 34px;
    border-bottom: 1.5px dotted var(--rule);
  }
  .blank-line--1 { top: 226px; }
  .back__notice {
    position: absolute; left: 0; right: 0; top: 244px;
    text-align: center; font-size: 10.5px; color: var(--muted); line-height: 1.5;
  }

  /* ---------- Front: contact card ---------- */
  .card--front { left: 610px; top: 413px; }
  .brand {
    position: absolute; left: 26px; top: 96px; width: 200px;
    display: flex; align-items: center; gap: 10px;
  }
  .brand__dot {
    flex: none; width: 22px; height: 22px; border-radius: 50%; background: var(--sky);
  }
  .brand__name {
    font-size: 20px; font-weight: 700; color: var(--sky); line-height: 1.15;
  }
  .divider {
    position: absolute; left: 238px; top: 58px; height: 150px;
    border-left: 1.5px solid var(--divider);
  }
  .contact { position: absolute; left: 252px; top: 56px; right: 10px; }
  .contact__name { font-size: 19px; font-weight: 700; color: var(--navy); line-height: 1.1; }
  .contact__role { font-size: 13px; color: var(--ink); margin-bottom: 10px; }
  .contact__address { font-size: 12.5px; line-height: 1.3; margin-bottom: 4px; }
  .contact__row {
    display: flex; align-items: center; gap: 8px;
    font-size: 12.5px; line-height: 1.55; white-space: nowrap;
  }
  .contact__row svg { width: 12px; height: 12px; flex: none; fill: var(--navy); }
  .front__wave { position: absolute; left: 0; top: 0; width: 540px; height: 310px; }
</style>
</head>
<body>

  <section class="card card--back" aria-label="Appointment card">
    <h2 class="back__title">Next Appointment</h2>

    <div class="field field--name">Name :<span class="field__line"></span></div>
    <div class="field field--time">Time :<span class="field__line"></span><span class="ampm">AM/PM</span></div>
    <div class="field field--date">Date :<span class="field__line"></span></div>

    <div class="days">
      <span class="day">Sun <span class="day__box"></span></span>
      <span class="day">Mon <span class="day__box"></span></span>
      <span class="day">Tue <span class="day__box"></span></span>
      <span class="day">Wed <span class="day__box"></span></span>
      <span class="day">Thu <span class="day__box"></span></span>
      <span class="day">Fri <span class="day__box"></span></span>
      <span class="day">Sat <span class="day__box"></span></span>
    </div>

    <div class="field field--note">Note :<span class="field__line"></span></div>
    <div class="blank-line blank-line--1"></div>

    <p class="back__notice">If you are unable to keep your appointment or<br>Please give me 24 hours notice to reschedule.</p>
  </section>

  <section class="card card--front" aria-label="Contact card">
    <svg class="front__wave" viewBox="0 0 540 310" aria-hidden="true">
      <defs>
        <linearGradient id="band" x1="0" y1="0" x2="1" y2="0">
          <stop offset="0" stop-color="#1b2f8a"/>
          <stop offset=".55" stop-color="#4aa3e0"/>
          <stop offset="1" stop-color="#1b2f8a"/>
        </linearGradient>
      </defs>
      <path d="M0 252 C150 232 310 252 540 292 L540 310 L0 310 Z" fill="url(#band)"/>
      <path d="M0 240 C160 214 320 238 540 283" fill="none" stroke="#454545" stroke-width="3.5"/>
      <path d="M60 228 C200 210 340 232 520 270" fill="none" stroke="#9a9a9a" stroke-width="1.5"/>
    </svg>

    <div class="brand">
      <span class="brand__dot"></span>
      <span class="brand__name">Harbourline Physiotherapy</span>
    </div>

    <div class="divider"></div>

    <div class="contact">
      <p class="contact__name">Daniel Reeve</p>
      <p class="contact__role">CEO/Founder</p>
      <p class="contact__address">58 Wexley Lane Marrowdale<br>NSW 2791</p>
      <p class="contact__row">
        <svg viewBox="0 0 16 16"><path d="M3 1l3 3-1.5 2c1 2 3 4 5 5L11.5 9.5l3 3L13 15C7 14 2 9 1 3z"/></svg>
        02 9481 2057
      </p>
      <p class="contact__row">
        <svg viewBox="0 0 16 16"><path d="M4 1h8v4H4zM1 6h14v7h-3v2H4v-2H1zM5 10v4h6v-4z"/></svg>
        02 9481 2057
      </p>
      <p class="contact__row">
        <svg viewBox="0 0 16 16"><path d="M1 3h14v10H1zM2 4v1l6 4 6-4V4z"/></svg>
        info@harbourlinephysio.example.com.au
      </p>
      <p class="contact__row">
        <svg viewBox="0 0 16 16"><circle cx="8" cy="8" r="7"/><path d="M1 8h14M8 1c3 3 3 11 0 14M8 1c-3 3-3 11 0 14" stroke="#fff" stroke-width="1" fill="none"/></svg>
        www.harbourlinephysio.example.com.au
      </p>
    </div>
  </section>

</body>
</html>
```